Smile club flyer design

I am launching an office smile club and would like a design that sits my branding and that is appealing to customers. I have a design (I need a new one) that has all the information.
My website is maplehavendentalcarekx.com
Brand color is green. The design can be any color

Target Market(s)

Ages 30+

Industry/Entity Type

Dental

Font styles to use
Serif

Requirements
Must have
• Appealing to patients

```html
<!DOCTYPE html>
<html lang="en">
<head>
<meta charset="utf-8">
<title>Smile Club Membership – Maplehaven Dental Care</title>
<link href="https://fonts.googleapis.com/css2?family=Playfair+Display:wght@800;900&family=Yellowtail&family=Oswald:wght@600;700&family=Montserrat:wght@500;600;700;800&family=Roboto+Condensed:wght@500;600&display=swap" rel="stylesheet">
<style>
:root{
  --backdrop:#141414;
  --paper-top:#f6f9ea;
  --paper-bottom:#eaf6d6;
  --green:#2f9e3f;
  --green-bright:#46b03d;
  --green-lime:#8fd84a;
  --green-dark:#0d5f2d;
  --green-deep:#0b8a3c;
  --green-title:#178a36;
  --brown:#b5793f;
  --ink:#1f2a1f;
  --white:#ffffff;
}
*{margin:0;padding:0;box-sizing:border-box}
html,body{width:956px;height:1200px;overflow:hidden;background:var(--backdrop)}
.flyer{
  position:absolute;left:165px;top:130px;width:627px;height:940px;overflow:hidden;
  background:linear-gradient(180deg,var(--paper-top) 0%,#f2f8e2 45%,var(--paper-bottom) 100%);
  font-family:"Montserrat",sans-serif;color:var(--ink);
}
.photo{
  position:absolute;left:320px;top:0;width:307px;height:346px;
  background:
    radial-gradient(ellipse at 62% 35%,#e8c4a8 0%,#d9b391 25%,rgba(217,179,145,0) 50%),
    linear-gradient(90deg,rgba(242,247,232,0) 0%,#cfd9d6 30%,#b8cad6 70%,#9fb7cc 100%);
}
.brand{
  position:absolute;left:0;top:0;width:245px;height:65px;
  background:linear-gradient(90deg,#2a9a3e,#5fbf3c);
  border-radius:0 33px 33px 0;
  display:flex;align-items:center;justify-content:center;padding-right:18px;
}
.brand-name{font-family:"Playfair Display",serif;font-weight:800;font-size:17px;color:var(--white);letter-spacing:.3px}
.intro{position:absolute;left:41px;top:86px;font-family:"Yellowtail",cursive;font-size:40px;color:var(--brown)}
.headline{position:absolute;left:40px;top:134px;font-family:"Playfair Display",serif;font-weight:900;color:var(--green-title);font-size:46px;line-height:46px;letter-spacing:-.5px}
.band{position:absolute;left:0;height:24px;border-radius:0 12px 12px 0;color:var(--white);font-weight:700;font-size:16px;line-height:24px;padding-left:41px;letter-spacing:-.3px}
.band-light{top:239px;width:300px;background:var(--green-lime)}
.band-dark{top:271px;width:279px;background:var(--green-dark)}

.plan{position:absolute;width:183px;height:263px;background:var(--white);border-radius:12px;box-shadow:0 3px 10px rgba(40,90,30,.15)}
.plan-core{left:24px;top:397px}
.plan-bright{left:221px;top:360px}
.plan-total{left:418px;top:319px}
.plan-fold{position:absolute;left:24px;top:-42px;width:136px;height:42px;background:var(--green-dark);clip-path:polygon(12% 0,88% 0,100% 100%,0 100%)}
.plan-tab{position:absolute;left:41px;top:-42px;width:101px;height:133px;background:linear-gradient(180deg,#1f8f3a,var(--green-bright));border-radius:0 0 51px 51px;text-align:center;color:var(--white)}
.plan-name{font-family:"Oswald",sans-serif;font-weight:700;font-size:17px;line-height:20px;margin-top:9px;letter-spacing:.2px}
.plan-type{font-size:9.5px;font-weight:500;letter-spacing:.3px;margin-top:1px}
.price-ring{position:absolute;left:14px;top:53px;width:73px;height:73px;border-radius:50%;border:1.5px solid rgba(255,255,255,.85);display:flex;flex-direction:column;align-items:center;justify-content:center}
.price{font-family:"Oswald",sans-serif;font-weight:700;font-size:30px;line-height:30px}
.per{font-size:8.5px;font-weight:500}
.plan-arc{position:absolute;left:0;top:0;width:183px;height:120px;overflow:visible}
.features{position:absolute;left:16px;top:116px;width:158px;list-style:none;font-family:"Roboto Condensed",sans-serif;font-weight:600;font-size:11.5px;line-height:15.5px;color:var(--ink)}
.features li{position:relative;padding-left:15px;margin-bottom:5px}
.features li svg{position:absolute;left:0;top:2px;width:11px;height:11px}
.plan-foot{position:absolute;left:16px;top:232px;width:151px;height:53px}
.plan-foot .fold{position:absolute;top:21px;width:16px;height:32px;background:var(--green-dark)}
.plan-foot .fold.l{left:0;clip-path:polygon(0 0,100% 0,100% 100%)}
.plan-foot .fold.r{right:0;clip-path:polygon(0 0,100% 0,0 100%)}
.plan-btn{position:absolute;left:15px;top:0;width:121px;height:53px;background:linear-gradient(180deg,var(--green-bright),#74c94a);border-radius:22px 22px 0 0;display:flex;align-items:center;justify-content:center}
.plan-btn span{display:block;border:1.5px solid var(--white);border-radius:16px;padding:3px 10px;font-family:"Oswald",sans-serif;font-weight:700;font-size:14px;color:var(--white);letter-spacing:.3px}

.finance-title{position:absolute;left:46px;top:706px;font-family:"Oswald",sans-serif;font-weight:700;font-size:22px;color:var(--green-dark);letter-spacing:.2px}
.lender{position:absolute;top:750px;font-weight:700;font-size:19px;color:#2f4a3a;display:flex;align-items:center;gap:6px}
.lender-a{left:43px}
.lender-b{left:223px}
.lender .mark{width:16px;height:16px;border-radius:50%;background:var(--green-bright)}

.cta{position:absolute;left:0;top:781px;width:430px;height:89px;background:var(--green-deep);color:var(--white)}
.cta-title{position:absolute;left:36px;top:14px;font-weight:700;font-size:27px;letter-spacing:-.6px}
.cta-phone{position:absolute;left:36px;top:48px;display:flex;align-items:center;gap:14px;font-weight:700;font-size:27px;letter-spacing:.5px}
.plans-note{position:absolute;left:37px;top:887px;font-weight:600;font-size:14px;color:#1e2a22;letter-spacing:-.2px}
.fee{position:absolute;left:0;top:907px;width:426px;height:33px;background:linear-gradient(90deg,#24963d,#6ccb3f);clip-path:polygon(0 0,100% 0,93% 100%,0 100%);color:var(--white);font-family:"Roboto Condensed",sans-serif;font-weight:600;font-size:17px;line-height:33px;padding-left:37px}

.package{position:absolute;left:431px;top:733px;width:182px;height:124px;background:linear-gradient(180deg,#8fd84a,#a3e35b);border-radius:14px}
.package-arc{position:absolute;left:438px;top:656px;width:170px;height:100px;overflow:visible}
.package-badge{position:absolute;left:450px;top:664px;width:142px;height:142px;border-radius:50%;background:linear-gradient(180deg,#2c9a3f,#3aa83c);border:4px solid var(--white);text-align:center;color:var(--white)}
.package-new{font-family:"Yellowtail",cursive;font-size:22px;line-height:22px;margin-top:12px}
.package-name{font-weight:800;font-size:28px;line-height:28px}
.package-sub{font-size:9px;font-weight:600;letter-spacing:-.1px}
.package-price{font-family:"Oswald",sans-serif;font-weight:700;font-size:36px;line-height:40px}
.package-detail{position:absolute;left:449px;top:822px;width:160px;font-family:"Roboto Condensed",sans-serif;font-weight:600;font-size:12.5px;line-height:15.5px;color:var(--green-dark);padding-left:15px}
.package-detail svg{position:absolute;left:0;top:2px;width:11px;height:11px}
.offer{position:absolute;left:443px;top:878px;width:159px;height:31px;border-radius:16px;background:var(--green-deep);color:var(--white);font-weight:700;font-size:12.5px;line-height:31px;text-align:center}
</style>
</head>
<body>
<svg width="0" height="0" style="position:absolute">
  <defs>
    <symbol id="tick" viewBox="0 0 12 12"><circle cx="6" cy="6" r="6" fill="#2f9e3f"/><path d="M3.3 6.2 5.2 8 8.8 4.2" fill="none" stroke="#fff" stroke-width="1.6" stroke-linecap="round" stroke-linejoin="round"/></symbol>
    <symbol id="arc" viewBox="0 0 183 120"><path d="M28 23 V45 A63.5 63 0 0 0 155 45 V23" fill="none" stroke="#8fd84a" stroke-width="2"/><circle cx="28" cy="23" r="4" fill="#8fd84a"/><circle cx="155" cy="23" r="4" fill="#8fd84a"/></symbol>
  </defs>
</svg>

<main class="flyer">
  <div class="photo" role="img" aria-label="Photo of a smiling patient in a dental chair with a dentist holding a mirror"></div>

  <div class="brand"><span class="brand-name">Maplehaven Dental Care</span></div>

  <div class="intro">Introducing</div>
  <h1 class="headline">SMILE CLUB<br>MEMBERSHIP</h1>
  <div class="band band-light">AFFORDABLE DENTAL CARE</div>
  <div class="band band-dark">NO INSURANCE REQUIRED</div>

  <section class="plan plan-core">
    <div class="plan-fold"></div>
    <svg class="plan-arc"><use href="#arc"/></svg>
    <div class="plan-tab">
      <div class="plan-name">CORE CARE</div>
      <div class="plan-type">PREVENTIVE</div>
      <div class="price-ring"><span class="price">$39</span><span class="per">/MONTH</span></div>
    </div>
    <ul class="features">
      <li><svg><use href="#tick"/></svg>Comprehensive Annual Exam</li>
      <li><svg><use href="#tick"/></svg>2 Professional Cleanings per Year</li>
      <li><svg><use href="#tick"/></svg>Routine Bitewing X-rays</li>
      <li><svg><use href="#tick"/></svg>10% Savings on Treatment</li>
    </ul>
    <div class="plan-foot"><div class="fold l"></div><div class="fold r"></div><div class="plan-btn"><span>$39/MONTH</span></div></div>
  </section>

  <section class="plan plan-bright">
    <div class="plan-fold"></div>
    <svg class="plan-arc"><use href="#arc"/></svg>
    <div class="plan-tab">
      <div class="plan-name">BRIGHT</div>
      <div class="plan-type">COSMETIC</div>
      <div class="price-ring"><span class="price">$59</span><span class="per">/MONTH</span></div>
    </div>
    <ul class="features">
      <li><svg><use href="#tick"/></svg>Annual In-Office Whitening (Top &amp; Bottom)</li>
      <li><svg><use href="#tick"/></svg>Custom Whitening Trays</li>
      <li><svg><use href="#tick"/></svg>15% Savings on Elective Treatment</li>
    </ul>
    <div class="plan-foot"><div class="fold l"></div><div class="fold r"></div><div class="plan-btn"><span>$59/MONTH</span></div></div>
  </section>

  <section class="plan plan-total">
    <div class="plan-fold"></div>
    <svg class="plan-arc"><use href="#arc"/></svg>
    <div class="plan-tab">
      <div class="plan-name">TOTAL SMILE</div>
      <div class="plan-type">PERIODONTAL</div>
      <div class="price-ring"><span class="price">$89</span><span class="per">/MONTH</span></div>
    </div>
    <ul class="features">
      <li><svg><use href="#tick"/></svg>3-4 Perio Maintenance Visits per Year</li>
      <li><svg><use href="#tick"/></svg>1 Comprehensive Exam</li>
      <li><svg><use href="#tick"/></svg>Diagnostic X-rays</li>
      <li><svg><use href="#tick"/></svg>15% Savings on Restorative &amp; Elective Care</li>
    </ul>
    <div class="plan-foot"><div class="fold l"></div><div class="fold r"></div><div class="plan-btn"><span>$89/MONTH</span></div></div>
  </section>

  <h2 class="finance-title">FLEXIBLE FINANCING FOR TREATMENT</h2>
  <div class="lender lender-a"><span class="mark"></span>FlexPay Health</div>
  <div class="lender lender-b"><span class="mark"></span>Orchard Pay</div>

  <section class="cta">
    <div class="cta-title">JOIN SMILE CLUB TODAY!</div>
    <div class="cta-phone">
      <svg width="16" height="16" viewBox="0 0 24 24" aria-hidden="true"><path d="M6.6 10.8a15.5 15.5 0 0 0 6.6 6.6l2.2-2.2a1 1 0 0 1 1-.25 11.4 11.4 0 0 0 3.6.57 1 1 0 0 1 1 1V20a1 1 0 0 1-1 1A17 17 0 0 1 3 4a1 1 0 0 1 1-1h3.5a1 1 0 0 1 1 1c0 1.25.2 2.45.57 3.57a1 1 0 0 1-.25 1z" fill="#fff"/></svg>
      <span>865-555-0142</span>
    </div>
  </section>

  <div class="plans-note">PAYMENT PLANS AVAILABLE</div>
  <div class="fee">*$49 Lifetime Activation Fee (Non-Refundable)</div>

  <div class="package"></div>
  <svg class="package-arc" viewBox="0 0 170 100"><path d="M7 52 A79 79 0 0 1 163 50" fill="none" stroke="#0b8a3c" stroke-width="2"/><circle cx="7" cy="53" r="4" fill="#0b8a3c"/><circle cx="163" cy="50" r="4" fill="#0b8a3c"/></svg>
  <div class="package-badge">
    <div class="package-new">New</div>
    <div class="package-name">SMILE</div>
    <div class="package-sub">REFRESH PACKAGE</div>
    <div class="package-price">$499</div>
  </div>
  <div class="package-detail"><svg><use href="#tick"/></svg>Cleaning + Comprehensive Exam + Whitening</div>
  <div class="offer">LIMITED TIME OFFER</div>
</main>
</body>
</html>
```